PWRPT design for Company

Project: Develop a pwrpt for QT7lx. This can be just a blank pwrpt with standard templates that we can use to build our content and solutions around.
Website: www.qt7lx.example
Color Pallet: Try to use the color schema from our website.
PWRPT Design Tips: While we are a research-based company, our primary target is schools and school districts. We say our work is RESEARCH, POLICY, AND PRACTICE. I would like images that represent “WHY” our research matters, i.e. students, teachers, and administrators. If you can use images and stock photos that represent students with diverse backgrounds, teachers that are diverse and clearly teaching, and administrators that run a school, university, etc. We are in the process of updating our website, but the color scheme will remain the same.
Additional Information:
We built, researched, and designed, www.brvo-kt.example .
We built, researched, and designed, http://67pwgamma.example/olar/index.html
Target Market(s)
EDUCATION
Industry/Entity Type
It Company
Look and feel

```html
<!DOCTYPE html>
<html lang="en">
<head>
<meta charset="utf-8">
<title>QT7lx – Welcome Slide</title>
<link rel="stylesheet" href="https://fonts.googleapis.com/css2?family=Montserrat:wght@800&family=Open+Sans:wght@400&display=swap">
<style>
  :root {
    --orange: #f47a20;
    --orange-light: #f79236;
    --slate: #4b525b;
    --slate-dark: #464c54;
    --brand-grey: #5d6670;
    --ink: #333333;
    --white: #ffffff;
    --photo-deep: #3f6b2a;
    --photo-mid: #7fa550;
    --photo-light: #b9cf8a;
  }
  * { box-sizing: border-box; margin: 0; padding: 0; }
  html, body { width: 1200px; height: 900px; overflow: hidden; background: var(--white); }
  .slide { position: relative; width: 1200px; height: 900px; overflow: hidden; background: var(--white); }

  .hero { position: absolute; left: 0; top: 0; width: 1200px; height: 735px; }
  .hero-photo {
    position: absolute; inset: 0;
    background: linear-gradient(160deg, var(--photo-deep) 0%, var(--photo-mid) 45%, var(--photo-light) 100%);
  }
  .hero-band { position: absolute; inset: 0; width: 1200px; height: 735px; }

  .hero-text { position: absolute; left: 665px; top: 530px; color: var(--white); }
  .hero-title {
    font-family: "Montserrat", sans-serif; font-weight: 800;
    font-size: 55px; letter-spacing: 0.5px; line-height: 1;
  }
  .hero-subtitle {
    font-family: "Open Sans", sans-serif; font-weight: 400;
    font-size: 37px; line-height: 1; margin-top: 12px;
  }
  .hero-date {
    font-family: "Open Sans", sans-serif; font-weight: 400;
    font-size: 25px; line-height: 1; margin-top: 22px;
  }

  .footer { position: absolute; left: 0; top: 735px; width: 1200px; height: 143px; background: var(--white); }
  .footer-legal {
    position: absolute; left: 40px; top: 55px; width: 665px;
    font-family: "Open Sans", sans-serif; font-size: 15.5px; line-height: 24px; color: var(--ink);
  }
  .brand {
    position: absolute; left: 860px; top: 46px;
    display: flex; align-items: center; gap: 14px;
  }
  .brand-square { width: 30px; height: 30px; background: var(--orange); }
  .brand-name {
    font-family: "Open Sans", sans-serif; font-weight: 400;
    font-size: 40px; line-height: 1; color: var(--brand-grey);
  }
  .base-bar { position: absolute; left: 0; top: 878px; width: 1200px; height: 22px; background: var(--slate-dark); }
</style>
</head>
<body>
<main class="slide">
  <section class="hero">
    <div class="hero-photo" role="img" aria-label="Photo of two smiling students sitting on the grass outdoors holding notebooks"></div>
    <svg class="hero-band" viewBox="0 0 1200 735" aria-hidden="true">
      <defs>
        <linearGradient id="bandFill" x1="0" y1="0" x2="1" y2="1">
          <stop offset="0" stop-color="#f79236"/>
          <stop offset="1" stop-color="#f47a20"/>
        </linearGradient>
      </defs>
      <polygon points="843,0 1200,0 1200,735 528,735" fill="#4b525b"/>
      <polygon points="858,0 1200,0 1200,735 543,735" fill="url(#bandFill)"/>
    </svg>
    <div class="hero-text">
      <h1 class="hero-title">WELCOME</h1>
      <p class="hero-subtitle">Route2Futures (R2F)</p>
      <p class="hero-date">August 21st, 2017</p>
    </div>
  </section>

  <footer class="footer">
    <p class="footer-legal">© 2017 All rights reserved. Contains confidential and proprietary information and may not be disclosed or reproduced without&nbsp; the prior written consent of QT7lx</p>
    <div class="brand">
      <span class="brand-square"></span>
      <span class="brand-name">QT7lx</span>
    </div>
  </footer>
  <div class="base-bar"></div>
</main>
</body>
</html>
```